Webdesign für Projektmanagement
Zielgruppe
Projektmanagement und Projektsteuerung von Bauvorhaben für Projektentwickler und Bauträger.
Wesentliche Bereiche sind Wirtschaftliche Steuerung, Steuerung der Baustelle und Bauabläufe sowie Steuerung der Marketing und Vertriebsaktivitäten.
Aufgabenstellung
Orientierung am Logo. Logo und Visitenkarte liegen bei. Schriftart Prelo und Prelo Slab.

```html
<!DOCTYPE html>
<html lang="de">
<head>
<meta charset="utf-8">
<title>Veldhaus Real Estate – Projektmanagement</title>
<link href="https://fonts.googleapis.com/css2?family=Bitter:ital,wght@0,400;0,600;0,700;1,400&family=Mulish:wght@300;400;600&display=swap" rel="stylesheet">
<style>
:root{
  --navy:#03233f;
  --gold:#a8955a;
  --paper:#f4f6f6;
  --white:#ffffff;
  --ink:#2b3a4a;
  --muted:#a9b0b8;
}
*{box-sizing:border-box;margin:0;padding:0}
html,body{width:1200px;height:3629px;overflow:hidden}
body{position:relative;background:var(--paper);font-family:"Mulish",sans-serif;color:var(--ink)}
.abs{position:absolute}
.slab{font-family:"Bitter",serif}

/* header */
.header-white{left:0;top:0;width:592px;height:165px;background:linear-gradient(#fff,#f4f6f6)}
.header-navy{left:592px;top:0;width:608px;height:518px;background:var(--navy)}
.brand{left:56px;top:58px}
.brand-name{font-family:"Bitter",serif;font-weight:700;font-size:38px;color:var(--navy);line-height:1}
.brand-sub{font-family:"Bitter",serif;font-weight:400;font-size:17px;color:var(--gold);margin-left:56px;line-height:1}
.nav{left:660px;top:68px;display:flex;gap:17px}
.nav a{color:#fff;text-decoration:none;font-size:19px;letter-spacing:.4px}

/* hero */
.hero-card{left:0;top:165px;width:840px;height:424px;background:#fff;box-shadow:0 10px 30px rgba(0,0,0,.04)}
.hero-art{left:56px;top:222px;width:620px;height:350px;border-radius:6px;background:radial-gradient(ellipse at center,#e6e9ee 0%,#f6f7f9 60%,#fff 100%)}
.hero-text{left:756px;top:298px;width:356px;height:342px;background:#fff;box-shadow:0 12px 36px rgba(3,35,63,.12);padding:68px 52px 0 53px}
.hero-text h1{font-family:"Bitter",serif;font-weight:600;font-size:21px;line-height:32px;color:var(--navy)}
.hero-text p{font-family:"Bitter",serif;font-size:18px;line-height:32px;color:var(--gold);margin-top:6px}

/* beratung */
.beratung-title{left:129px;top:778px;font-family:"Bitter",serif;font-weight:600;font-size:28px;line-height:39px;color:var(--navy)}
.btn-gold{left:130px;top:882px;width:147px;height:36px;background:var(--gold);color:#fff;font-size:13px;display:flex;align-items:center;justify-content:center;box-shadow:0 6px 14px rgba(168,149,90,.35)}
.beratung-copy{left:610px;top:783px;width:440px;font-size:14px;line-height:28px;color:#3b4856}
.beratung-copy p+p{margin-top:16px}

/* about band */
.about-band{left:0;top:1220px;width:1200px;height:518px;background:var(--navy)}
.about-text{left:347px;top:1350px;width:520px;font-family:"Bitter",serif;font-size:20px;line-height:34px;color:#fff}
.skyline{left:230px;top:1572px;width:740px;height:166px;background:linear-gradient(#0a2e4c,#12385a)}

/* referenzen */
.ref-title{left:129px;top:1838px;font-family:"Bitter",serif;font-weight:600;font-size:28px;color:var(--navy)}
.tabs{left:129px;top:1910px;display:flex;gap:78px;font-size:20px;letter-spacing:.3px}
.tab{color:var(--muted);padding-bottom:8px}
.tab.active{color:var(--navy);border-bottom:2px solid var(--navy)}
.ref-card{top:2025px;width:546px;height:243px;background:#fff;box-shadow:0 14px 34px rgba(3,35,63,.08);display:flex}
.ref-photo{width:212px;height:243px;background:linear-gradient(160deg,#8fb6d8 0%,#e9e6de 45%,#c9b79a 100%)}
.ref-body{padding:26px 34px 0 35px;width:334px}
.ref-body h3{font-family:"Bitter",serif;font-weight:700;font-size:12px;color:var(--navy)}
.ref-body .addr{font-family:"Bitter",serif;font-size:11px;color:var(--gold);margin-top:6px}
.ref-body p{font-size:14px;line-height:21px;color:#3b4856;margin-top:22px}
.ref-sliver{left:1140px;top:2025px;width:60px;height:243px;background:linear-gradient(#3a4a78,#6e6f86 60%,#a28a7a)}

/* karriere */
.career-band{left:0;top:2410px;width:1200px;height:548px;background:var(--navy)}
.career-title{left:128px;top:2527px;font-family:"Bitter",serif;font-weight:600;font-size:28px;color:#fff}
.career-sub{left:130px;top:2569px;font-family:"Bitter",serif;font-style:italic;font-size:21px;color:#fff}
.career-copy{left:130px;top:2633px;width:330px;font-size:14px;line-height:28px;color:#fff}
.btn-outline{left:128px;top:2787px;width:143px;height:37px;border:1px solid #fff;color:#fff;font-size:12px;letter-spacing:.4px;display:flex;align-items:center;justify-content:center}
.career-photo{left:573px;top:2532px;width:627px;height:436px;background:linear-gradient(100deg,#dfe9ef 0%,#c6d8e2 45%,#d9b69a 55%,#8aa0ad 80%,#5e7784 100%)}

/* map */
.map{left:0;top:2958px;width:1200px;height:367px;background:linear-gradient(135deg,#eeeff0,#e5e7e9)}
.pin{left:560px;top:3087px}

/* standort */
.site-title{left:128px;top:3392px;font-family:"Bitter",serif;font-weight:600;font-size:28px;color:var(--navy)}
.address{left:757px;top:3400px;font-size:14px;line-height:25px;color:#3b4856}
.address strong{font-weight:600;color:var(--navy)}
</style>
</head>
<body>

<div class="abs header-white"></div>
<div class="abs header-navy"></div>

<div class="abs brand">
  <div class="brand-name">Veldhaus</div>
  <div class="brand-sub">Real Estate</div>
</div>

<nav class="abs nav">
  <a href="#">Home</a><a href="#">Leistungen</a><a href="#">Referenzen</a><a href="#">Über Uns</a><a href="#">Kontakt</a>
</nav>

<div class="abs hero-card"></div>
<div class="abs hero-art" role="img" aria-label="Illustration eines Projektmanagers, umgeben von Symbolen für Planung, Kosten und Termine"></div>
<div class="abs hero-text">
  <h1>Projektmanagement und Projektsteuerung von Bauvorhaben</h1>
  <p>für Projektentwickler und Bauträger</p>
</div>

<h2 class="abs beratung-title">Ganzheitliche<br>Beratung</h2>
<div class="abs btn-gold">Jetzt beraten lassen</div>
<div class="abs beratung-copy">
  <p>Die zunehmende Urbanisierung hat den Immobilienmarkt in den letzten Jahren nachhaltig verändert. Als Teil des größten Ballungszentrums Europas, hat dies starke Auswirkungen auf die Metropolregion Köln, Düsseldorf und Bonn. Begleitet wird diese Entwicklung durch vielschichtige städtebauliche Maßnahmen in der Region.</p>
  <p>Die Konsequenz aus dieser Entwicklung ist ein hoher Investitions-, Umnutzungs- und Projektentwicklungsbedarf bei Immobilien. Daraus entstanden ist ein für Investoren strukturell attraktiver Markt.</p>
</div>

<div class="abs about-band"></div>
<p class="abs about-text">Wir sind ein interdisziplinär tätiges, mittelständisches Beratungs- und Dienstleistungsunternehmen. Wir bieten unseren Kunden maßgeschneiderte Dienstleis­tungen für ihr Immobilienportfolios an.</p>
<div class="abs skyline" role="img" aria-label="Stilisierte Stadtsilhouette mit Bäumen und goldener Sonne"></div>

<h2 class="abs ref-title">Unsere Referenzen</h2>
<div class="abs tabs">
  <span class="tab active">Immobiliensanierung</span>
  <span class="tab">Immobilienmanagement</span>
  <span class="tab">Immobilienvertrieb und -marketing</span>
</div>

<article class="abs ref-card" style="left:44px">
  <div class="ref-photo" role="img" aria-label="Foto eines weißen Wohnhauses mit Garage"></div>
  <div class="ref-body">
    <h3>Parkline Stage One</h3>
    <div class="addr">24 Harbour Lane, Westgrove</div>
    <p>Parkline is a new pocket neighbourhood where considered apartment living meets shared green spaces in one of Auckland's oldest urban villages. To be developed over two stages, it will comprise 239 apartments.</p>
  </div>
</article>
<article class="abs ref-card" style="left:593px">
  <div class="ref-photo" role="img" aria-label="Foto eines weißen Wohnhauses mit Garage"></div>
  <div class="ref-body">
    <h3>Parkline Stage One</h3>
    <div class="addr">24 Harbour Lane, Westgrove</div>
    <p>Parkline is a new pocket neighbourhood where considered apartment living meets shared green spaces in one of Auckland's oldest urban villages. To be developed over two stages, it will comprise 239 apartments.</p>
  </div>
</article>
<div class="abs ref-sliver" role="img" aria-label="Foto einer Stadt in der Abenddämmerung"></div>

<div class="abs career-band"></div>
<h2 class="abs career-title">Karriere bei Veldhaus</h2>
<div class="abs career-sub">wir suchen Verstärkung</div>
<p class="abs career-copy">Wir sind ständig auf der Suche nach qualifizierten Mitarbeiterinnen und Mitarbeitern um unser Team von 60 Mitarbeitern weiter zu verstärken.</p>
<div class="abs btn-outline">JETZT BEWERBEN</div>
<div class="abs career-photo" role="img" aria-label="Foto eines Händedrucks zweier Geschäftsleute"></div>

<div class="abs map" role="img" aria-label="Karte der Region Düsseldorf mit Standortmarkierung"></div>
<svg class="abs pin" width="40" height="56" viewBox="0 0 40 56" aria-hidden="true">
  <path d="M20 2C10 2 2 10 2 20c0 13 18 34 18 34s18-21 18-34C38 10 30 2 20 2z" fill="#a8955a"/>
  <circle cx="20" cy="20" r="8" fill="#fff"/>
</svg>

<h2 class="abs site-title">Unser Standort</h2>
<address class="abs address" style="font-style:normal">
  <strong>Veldhaus Real Estate GmbH</strong><br>
  Lindenhofstr. 12<br>
  40210 Düsseldorf<br>
  Tel: +49(0)211 – 555 01 20<br>
  Fax: +49(0)211 – 555 01 29<br>
  E-Mail: info@veldhaus-immo.de
</address>

</body>
</html>
```